Cool Website Design Gleam Shell Crew.

We need a new website, using our existing domain, with a similar function to https://www.marbeckfilm.com/ or https://www.tolvanfinishworks.com/ instagram gleam_shell.crew.
We can send google docs with pictures.
Logo attached

```html
<!DOCTYPE html>
<html lang="en">
<head>
<meta charset="utf-8">
<title>Gleam Shell Crew — Premium Vehicle Wraps</title>
<link rel="stylesheet" href="https://fonts.googleapis.com/css2?family=Montserrat:wght@400;500;600;700&display=swap">
<style>
:root{
  --bg:#252525;
  --bg-deep:#1b1b1f;
  --panel:#1e1e27;
  --card:#4b4949;
  --ink:#ffffff;
  --ink-soft:#d6d6d6;
  --purple:#7a3fe2;
  --blue:#1ea8f0;
  --grad:linear-gradient(90deg,var(--purple),var(--blue));
  --star:#f7c21b;
  --line:#8a8a8a;
}
*{box-sizing:border-box;margin:0;padding:0}
html,body{width:1200px;height:3665px;overflow:hidden}
body{position:relative;background:var(--bg);color:var(--ink);font-family:"Montserrat",sans-serif}
.abs{position:absolute}
a{color:inherit;text-decoration:none}
.btn{position:absolute;display:flex;align-items:center;justify-content:center;background:var(--grad);color:#fff;font-size:16px;font-weight:500;border-radius:7px}

/* header & hero */
.hero{position:absolute;left:0;top:0;width:1200px;height:760px;
  background:radial-gradient(ellipse at 12% 20%,rgba(122,63,226,.35),transparent 45%),
             radial-gradient(ellipse at 88% 30%,rgba(30,168,240,.3),transparent 45%),#1f1f22}
.brand{position:absolute;display:flex;align-items:center;gap:10px;font-weight:700;color:var(--purple);letter-spacing:.5px}
.brand .mark{width:16px;height:16px;background:var(--purple)}
.nav a{position:absolute;top:46px;font-size:17px;font-weight:500}
.nav .current{font-weight:700;border-bottom:2px solid #fff;padding-bottom:2px}
.hero h1{position:absolute;left:0;width:1200px;top:166px;text-align:center;font-size:46px;line-height:51px;font-weight:700;text-shadow:0 2px 8px rgba(0,0,0,.6)}
.hero .lead{position:absolute;left:0;width:1200px;top:296px;text-align:center;font-size:18px;line-height:28px}
.hero-visual{position:absolute;left:242px;top:455px;width:712px;height:264px;border-radius:60px 80px 30px 30px;
  background:linear-gradient(180deg,#cfd2d4,#6b6e71 70%,#2b2c2e)}

/* reviews */
.section-title{position:absolute;font-size:37px;line-height:44px;font-weight:600;text-shadow:0 2px 6px rgba(0,0,0,.5)}
.review-badge{position:absolute;left:937px;top:814px;width:152px;height:69px;border-radius:10px;background:#3a3a3a}
.review{position:absolute;top:948px;width:310px;height:225px;background:var(--card);border-radius:10px;padding:42px 25px 0}
.review p{font-size:14px;line-height:21.5px;color:#f0f0f0}
.review .quote{position:absolute;right:20px;top:-38px;font-size:96px;line-height:96px;font-weight:700;color:#fff;text-shadow:0 0 0 #000,3px 3px 0 #1a1a1a}
.review .name{position:absolute;left:25px;top:168px;font-size:16px;font-weight:600}
.review .stars{position:absolute;left:25px;top:188px;font-size:14px;color:var(--star);letter-spacing:-1px}
.review .source{position:absolute;right:25px;top:166px;width:38px;height:38px;border-radius:50%;border:6px solid #e8e8e8}
.dots{position:absolute;left:568px;top:1195px;display:flex;gap:6px}
.dots i{width:11px;height:11px;border-radius:50%;border:1.5px solid #fff}
.dots i.on{background:#fff}

/* services */
.services{position:absolute;left:111px;top:1293px;width:978px;height:858px;border-radius:22px;
  background:linear-gradient(160deg,#202027,#17171e 60%,#1d1d2a)}
.service{position:absolute;width:406px;height:249px;border:1.5px solid #d8d8d8;border-radius:12px;text-align:center}
.service.active{background:var(--grad);border:none}
.service.active::after{content:"";position:absolute;inset:10px;border:1.5px solid #fff;border-radius:10px}
.service .icon{position:absolute;left:153px;top:22px;width:100px;height:100px;border-radius:50%;background:#fff;border:8px solid #111;display:flex;align-items:center;justify-content:center}
.service.active .icon{border-color:#6d4be6}
.service h3{position:absolute;left:0;right:0;top:148px;font-size:19px;font-weight:500}
.service p{position:absolute;left:50px;right:50px;top:184px;font-size:14px;line-height:17px;color:var(--ink-soft)}

/* vision */
.vision-name{position:absolute;left:112px;top:2430px;width:386px;font-size:34px;line-height:40px;font-weight:700;color:var(--purple)}
.vision-copy{position:absolute;left:601px;top:2230px;width:488px}
.vision-copy strong{display:block;font-size:17px;line-height:27px;font-weight:600;margin-bottom:16px}
.vision-copy p{font-size:17px;line-height:27.5px;color:#e6e6e6;margin-bottom:8px}

/* gallery */
.shot{position:absolute;border-radius:6px}
.arrow{position:absolute;top:3062px;width:40px;height:40px;border-radius:50%;display:flex;align-items:center;justify-content:center}

/* cta & footer */
.cta{position:absolute;left:0;top:3189px;width:1200px;height:476px;background:linear-gradient(180deg,#1f1f22,#18181b)}
.cta h2{position:absolute;left:112px;top:3270px;font-size:37px;font-weight:600}
.cta-text{position:absolute;left:114px;top:3332px;font-size:16px}
.rule{position:absolute;left:111px;top:3435px;width:978px;height:1px;background:var(--line)}
.foot-nav a{position:absolute;top:3574px;font-size:19px;transform:translateX(-50%)}
.copyright{position:absolute;left:0;top:3623px;width:1200px;height:42px;background:#111;font-size:13px;display:flex;align-items:center;justify-content:center}
</style>
</head>
<body>

<header class="hero">
  <div class="brand" style="left:112px;top:36px;font-size:19px"><span class="mark"></span>GLEAM SHELL CREW</div>
  <nav class="nav">
    <a class="current" style="left:497px" href="#">Home</a>
    <a style="left:602px" href="#">About Us</a>
    <a style="left:731px" href="#">Services</a>
    <a style="left:850px" href="#">Gallery</a>
  </nav>
  <a class="btn" style="left:958px;top:41px;width:131px;height:36px" href="#">Contact</a>
  <h1>Premium<br>Vehicle Wraps &amp; Custom Graphics</h1>
  <p class="lead">Transform your ride with high-quality vinyl wraps, expert installation,<br>and standout designs.</p>
  <a class="btn" style="left:485px;top:370px;width:230px;height:37px" href="#">Book Your Free Quote</a>
  <div class="hero-visual" role="img" aria-label="Side view of a white hatchback rally car with black camouflage wrap and sponsor lettering"></div>
</header>

<h2 class="section-title" style="left:112px;top:804px">What Customers Say<br>About Us</h2>
<div class="review-badge" role="img" aria-label="Review listing badge"></div>

<div class="review" style="left:111px">
  <span class="quote">“</span>
  <p>“Lorem ipsum dolor sit amet, consec tetur adipiscing elit, sed do eiusmod tempor incid idunt ut labore et do lore magna aliqua. Quis ipsum susp end isse ultrices gravida. “</p>
  <span class="name">Dana Morrow</span><span class="stars">★★★★★</span><span class="source"></span>
</div>
<div class="review" style="left:444px">
  <span class="quote">“</span>
  <p>“Lorem ipsum dolor sit amet, consec tetur adipiscing elit, sed do eiusmod tempor incid idunt ut labore et do lore magna aliqua. Quis ipsum susp end isse ultrices gravida. “</p>
  <span class="name">Dana Morrow</span><span class="stars">★★★★★</span><span class="source"></span>
</div>
<div class="review" style="left:777px">
  <span class="quote">“</span>
  <p>“Lorem ipsum dolor sit amet, consec tetur adipiscing elit, sed do eiusmod tempor incid idunt ut labore et do lore magna aliqua. Quis ipsum susp end isse ultrices gravida. “</p>
  <span class="name">Dana Morrow</span><span class="stars">★★★★★</span><span class="source"></span>
</div>
<div class="dots"><i class="on"></i><i></i><i></i><i></i></div>

<section class="services"></section>
<h2 class="section-title" style="left:0;width:1200px;text-align:center;top:1372px">Our Services</h2>

<div class="service" style="left:182px;top:1462px">
  <div class="icon"><svg width="44" height="30" viewBox="0 0 44 30"><rect x="2" y="10" width="40" height="12" rx="4" fill="none" stroke="#4b5fe0" stroke-width="3"/><circle cx="12" cy="23" r="4" fill="#7a3fe2"/><circle cx="32" cy="23" r="4" fill="#7a3fe2"/></svg></div>
  <h3>Commercial Wraps</h3><p>Increase brand visibility with bold, durable fleet wraps.</p>
</div>
<div class="service active" style="left:612px;top:1462px">
  <div class="icon"><svg width="26" height="34" viewBox="0 0 26 34"><path d="M13 2C8 11 3 17 3 23a10 10 0 0 0 20 0C23 17 18 11 13 2z" fill="#6d4be6"/></svg></div>
  <h3>Color Change Wraps</h3><p>Refresh your vehicle with a new vibrant look.</p>
</div>
<div class="service" style="left:182px;top:1738px">
  <div class="icon"><svg width="44" height="30" viewBox="0 0 44 30"><path d="M4 20l6-10h20l8 10z" fill="none" stroke="#4b5fe0" stroke-width="3"/><circle cx="12" cy="22" r="4" fill="#7a3fe2"/><circle cx="32" cy="22" r="4" fill="#7a3fe2"/></svg></div>
  <h3>Paint Protection Film</h3><p>Protect your investment from chips, scratches, and road wear.</p>
</div>
<div class="service" style="left:612px;top:1738px">
  <div class="icon"><svg width="40" height="40" viewBox="0 0 40 40" fill="none" stroke="#6d4be6" stroke-width="3"><circle cx="20" cy="14" r="9"/><circle cx="13" cy="25" r="9"/><circle cx="27" cy="25" r="9"/></svg></div>
  <h3>Custom Graphics &amp; Decals</h3><p>Stand out with branding, lettering, or one-off custom designs.</p>
</div>
<a class="btn" style="left:537px;top:2028px;width:126px;height:36px" href="#">View More</a>

<h2 class="section-title" style="left:112px;top:2230px">Bringing Your Vision<br>To The Road</h2>
<div class="vision-name">GLEAM SHELL CREW</div>
<div class="vision-copy">
  <strong>Lorem ipsum dolor sit amet, consectetur adipiscing elit, sed do eiusmod</strong>
  <p>Sed ut perspiciatis unde omnis iste natus error sit volup tatem accusantium doloremque laudantium, totam rem aperiam, eaque ipsa quae ab illo inventore veritatis et quasi architecto beatae vitae dicta sunt explicabo. Nemo enim ipsam voluptatem quia voluptas</p>
  <p>Lorem ipsum dolor sit amet, consectetur adipiscing elit, sed do eiusmod tempor incididunt ut labore et dolore magna aliqua.</p>
</div>
<a class="btn" style="left:601px;top:2547px;width:126px;height:34px" href="#">Read More</a>

<h2 class="section-title" style="left:0;width:1200px;text-align:center;top:2661px">Featured Wraps Gallery</h2>
<div class="shot" style="left:112px;top:2769px;width:277px;height:244px;background:linear-gradient(135deg,#5a6170,#2f3440)" role="img" aria-label="Grey car door with blue hexagon graphic wrap"></div>
<div class="shot" style="left:409px;top:2757px;width:382px;height:266px;background:linear-gradient(135deg,#4a4d55,#2b2e34 55%,#c35a2a)" role="img" aria-label="Installer applying orange and black striped wrap to a sports car"></div>
<div class="shot" style="left:813px;top:2769px;width:276px;height:244px;background:linear-gradient(135deg,#3a3a3d,#1e1e20)" role="img" aria-label="Hands stretching matte black vinyl over a car panel"></div>
<span class="arrow" style="left:553px;border:2px solid var(--purple)"><svg width="12" height="14" viewBox="0 0 12 14"><path d="M8 2L3 7l5 5" fill="none" stroke="var(--blue)" stroke-width="2"/></svg></span>
<span class="arrow" style="left:608px;background:var(--grad)"><svg width="12" height="14" viewBox="0 0 12 14"><path d="M4 2l5 5-5 5" fill="none" stroke="#fff" stroke-width="2"/></svg></span>

<footer class="cta">
</footer>
<h2 class="cta-heading section-title" style="left:112px;top:3270px">Ready to Wrap Your Ride?</h2>
<p class="cta-text">Contact us today or request a free quote. Your vehicle deserves the best.</p>
<a class="btn" style="left:860px;top:3294px;width:229px;height:37px" href="#">Book Your Free Quote</a>
<div class="rule"></div>
<div class="brand" style="left:0;width:1200px;justify-content:center;top:3496px;font-size:19px"><span class="mark"></span>GLEAM SHELL CREW</div>
<nav class="foot-nav">
  <a style="left:318px" href="#">Home</a>
  <a style="left:448px" href="#">About Us</a>
  <a style="left:587px" href="#">Services</a>
  <a style="left:716px" href="#">Gallery</a>
  <a style="left:857px" href="#">Contact Us</a>
</nav>
<div class="copyright">Copyright © 2025 Gleam Shell Crew. All rights reserved.</div>

</body>
</html>
```